Business Card for Coastal Tundrabridge Advisory

We need a business card for Coastal Tundrabridge Advisory. The company website address is provided below. The company logo is attached. We provide specialized permafrost services to the mining, transportation, and oil & gas industries. The card should be prepared for:
Matthias Korhonen, PhD.
Coastal Tundrabridge Advisory
PO Box 418259
Quillwater, Alaska 99642
Direct: +1-907-555-0143
Email: mkorhonen@tundrabridgeadvisory.example
Website: www.coastaltundrabridgeadvisory.example

```html
<!DOCTYPE html>
<html lang="en">
<head>
<meta charset="utf-8">
<title>Coastal Tundrabridge Advisory – Business Card</title>
<link rel="stylesheet" href="https://fonts.googleapis.com/css2?family=Roboto+Condensed:wght@400;700&display=swap">
<style>
  :root {
    --backdrop: #ececec;
    --card-front: #ffffff;
    --card-back: #3a3a3a;
    --ink: #111111;
    --ink-soft: #1e1e1e;
    --icon-bar: #8c8c8c;
    --icon-ink: #ffffff;
    --back-mark: #161616;
  }
  html, body {
    margin: 0;
    padding: 0;
    width: 1200px;
    height: 1200px;
    overflow: hidden;
    background: var(--backdrop);
    font-family: "Roboto Condensed", Arial, sans-serif;
    color: var(--ink);
  }
  .canvas {
    position: relative;
    width: 1200px;
    height: 1200px;
  }
  .card {
    position: absolute;
    left: 236px;
    width: 727px;
    height: 416px;
    border-radius: 34px;
  }
  .card--front { top: 152px; background: var(--card-front); }
  .card--back  { top: 651px; background: var(--card-back); }

  .brand {
    position: absolute;
    left: 40px;
    top: 176px;
    width: 300px;
    text-align: center;
    font-weight: 700;
    color: var(--ink);
    text-transform: uppercase;
    line-height: 1;
  }
  .brand__line1 { font-size: 27px; letter-spacing: 1px; }
  .brand__line2 { font-size: 15px; letter-spacing: 8px; margin-top: 8px; }

  .person {
    position: absolute;
    left: 384px;
    top: 74px;
  }
  .person__name {
    font-weight: 700;
    font-size: 22px;
    text-transform: uppercase;
    margin: 0;
    letter-spacing: 0.2px;
  }
  .person__title {
    font-size: 15px;
    margin: 4px 0 0;
    color: var(--ink-soft);
  }

  .contacts {
    position: absolute;
    left: 384px;
    top: 156px;
  }
  .contacts__bar {
    position: absolute;
    left: 0;
    top: 0;
    width: 26px;
    height: 112px;
    border-radius: 6px;
    background: var(--icon-bar);
  }
  .contacts__list {
    list-style: none;
    margin: 0;
    padding: 0;
  }
  .contacts__item {
    position: relative;
    height: 28px;
    display: flex;
    align-items: center;
    font-size: 15px;
    color: var(--ink-soft);
  }
  .contacts__icon {
    position: absolute;
    left: 6px;
    width: 14px;
    height: 14px;
  }
  .contacts__text { margin-left: 44px; white-space: nowrap; }

  .address {
    position: absolute;
    left: 384px;
    top: 298px;
    font-size: 15px;
    line-height: 24px;
    color: var(--ink-soft);
  }

  .back-mark {
    position: absolute;
    left: 0;
    right: 0;
    top: 158px;
    text-align: center;
    font-weight: 700;
    color: var(--back-mark);
    text-transform: uppercase;
    line-height: 1;
  }
  .back-mark__line1 { font-size: 54px; letter-spacing: 3px; }
  .back-mark__line2 { font-size: 20px; letter-spacing: 16px; margin-top: 14px; }
</style>
</head>
<body>
<main class="canvas">

  <section class="card card--front" aria-label="Business card front">
    <div class="brand">
      <div class="brand__line1">Coastal Tundrabridge</div>
      <div class="brand__line2">Advisory</div>
    </div>

    <div class="person">
      <h1 class="person__name">Matthias Korhonen, PhD</h1>
      <p class="person__title">Founder &amp; Director</p>
    </div>

    <div class="contacts">
      <div class="contacts__bar"></div>
      <ul class="contacts__list">
        <li class="contacts__item">
          <svg class="contacts__icon" viewBox="0 0 24 24" aria-hidden="true"><path fill="var(--icon-ink)" d="M6.6 10.8a15.2 15.2 0 0 0 6.6 6.6l2.2-2.2a1 1 0 0 1 1-.25 11.4 11.4 0 0 0 3.6.57 1 1 0 0 1 1 1V20a1 1 0 0 1-1 1A17 17 0 0 1 3 4a1 1 0 0 1 1-1h3.5a1 1 0 0 1 1 1c0 1.25.2 2.45.57 3.6a1 1 0 0 1-.25 1z"/></svg>
          <span class="contacts__text">+1-907-555-0143</span>
        </li>
        <li class="contacts__item">
          <svg class="contacts__icon" viewBox="0 0 24 24" aria-hidden="true"><rect x="7" y="2.5" width="10" height="19" rx="2" fill="none" stroke="var(--icon-ink)" stroke-width="2"/></svg>
          <span class="contacts__text">(907) 555 0177</span>
        </li>
        <li class="contacts__item">
          <svg class="contacts__icon" viewBox="0 0 24 24" aria-hidden="true"><rect x="3" y="6" width="18" height="12" rx="1.5" fill="var(--icon-ink)"/><path d="M3.5 7l8.5 6 8.5-6" fill="none" stroke="var(--icon-bar)" stroke-width="1.5"/></svg>
          <span class="contacts__text">mkorhonen@tundrabridgeadvisory.example</span>
        </li>
        <li class="contacts__item">
          <svg class="contacts__icon" viewBox="0 0 24 24" aria-hidden="true"><g fill="none" stroke="var(--icon-ink)" stroke-width="2"><circle cx="12" cy="12" r="9"/><ellipse cx="12" cy="12" rx="4" ry="9"/><path d="M3 12h18"/></g></svg>
          <span class="contacts__text">www.coastaltundrabridgeadvisory.example</span>
        </li>
      </ul>
    </div>

    <address class="address" style="font-style:normal">
      PO Box 418259<br>
      Quillwater, Alaska 99642
    </address>
  </section>

  <section class="card card--back" aria-label="Business card back">
    <div class="back-mark">
      <div class="back-mark__line1">Coastal Tundrabridge</div>
      <div class="back-mark__line2">Advisory</div>
    </div>
  </section>

</main>
</body>
</html>
```